Business Card Design

New business card design

Target Market(s)

Residential & Commercial Property Managers

Industry/Entity Type

Plumbing Services

Contact Information for Business Card

Name - Rowan Keddle, title - Director, Phone Number - 0431 286 517, email - rowan@tbk-plumbing.com.au, Company ABN - 73 215 904 386,

Font styles to use
Sans Serif

Colors
0054AA
0677BA
7BADD7
CADEEF
E8F1F8

```html
<!DOCTYPE html>
<html lang="en">
<head>
<meta charset="utf-8">
<title>TBK Plumbing Services – Business Card</title>
<link href="https://fonts.googleapis.com/css2?family=Michroma&family=Roboto:wght@400&display=swap" rel="stylesheet">
<style>
  :root {
    --backdrop: #c4c4c4;
    --card: #1d232a;
    --accent: #00aeef;
    --white: #ffffff;
    --slate: #46607a;
  }
  html, body {
    margin: 0;
    padding: 0;
    width: 1093px;
    height: 1200px;
    overflow: hidden;
    background: var(--backdrop);
  }
  .card {
    position: absolute;
    left: 257px;
    width: 580px;
    height: 356px;
    border-radius: 30px;
    background: var(--card);
    overflow: hidden;
  }
  .card--front { top: 226px; }
  .card--back { top: 621px; }

  .brand__name,
  .brand__tagline {
    position: absolute;
    margin: 0;
    font-family: "Roboto", sans-serif;
    font-weight: 400;
    line-height: 1;
    white-space: nowrap;
  }
  .card--front .brand__name {
    left: 25px; top: 34px;
    font-size: 54px;
    color: var(--white);
  }
  .card--front .brand__tagline {
    left: 35px; top: 106px;
    font-size: 9px;
    letter-spacing: 9.4px;
    color: var(--white);
  }
  .card--back .brand__name {
    left: 0; right: 0; top: 104px;
    text-align: center;
    font-size: 82px;
    color: var(--slate);
  }
  .card--back .brand__tagline {
    left: 0; right: 0; top: 220px;
    text-align: center;
    font-size: 11px;
    letter-spacing: 16px;
    text-indent: 16px;
    color: var(--slate);
  }

  .tab {
    position: absolute;
    left: -18px; top: 166px;
    width: 36px; height: 36px;
    border-radius: 50%;
    background: var(--accent);
  }
  .person { position: absolute; left: 25px; top: 160px; }
  .person__name {
    font-family: "Michroma", sans-serif;
    font-size: 21px;
    color: var(--white);
    margin: 0;
    line-height: 1.2;
  }
  .person__title {
    font-family: "Roboto", sans-serif;
    font-size: 17px;
    color: var(--accent);
    margin: 0;
    line-height: 1.1;
  }
  .contact {
    position: absolute;
    left: 26px; top: 238px;
    font-family: "Roboto", sans-serif;
    font-size: 17px;
    color: var(--white);
    margin: 0; padding: 0;
    list-style: none;
  }
  .contact li { display: flex; align-items: center; gap: 7px; height: 21px; }
  .contact svg { width: 16px; height: 16px; fill: var(--accent); }
  .abn {
    position: absolute;
    left: 26px; top: 296px;
    font-family: "Roboto", sans-serif;
    font-size: 17px;
    color: var(--white);
    margin: 0;
  }
  .accent-band {
    position: absolute;
    left: 452px; top: 0;
    width: 128px; height: 356px;
    background: var(--accent);
  }
  .drop-art {
    position: absolute;
    left: 323px; top: 0;
    width: 257px; height: 356px;
    background: linear-gradient(160deg, var(--white) 55%, #d6f1fc 80%, var(--accent) 100%);
    border-radius: 130px 0 0 140px;
  }
</style>
</head>
<body>
  <section class="card card--front">
    <div class="accent-band"></div>
    <div class="drop-art" role="img" aria-label="Large water droplet graphic in white and blue"></div>

    <p class="brand__name">TBK</p>
    <p class="brand__tagline">plumbing services</p>

    <span class="tab"></span>
    <div class="person">
      <p class="person__name">Rowan Keddle</p>
      <p class="person__title">Director</p>
    </div>

    <ul class="contact">
      <li>
        <svg viewBox="0 0 24 24" aria-hidden="true"><path d="M6.6 10.8c1.4 2.8 3.8 5.1 6.6 6.6l2.2-2.2c.3-.3.7-.4 1-.2 1.1.4 2.3.6 3.6.6.6 0 1 .4 1 1V20c0 .6-.4 1-1 1C10.6 21 3 13.4 3 4c0-.6.4-1 1-1h3.5c.6 0 1 .4 1 1 0 1.3.2 2.5.6 3.6.1.3 0 .7-.2 1z"/></svg>
        0431 286 517
      </li>
      <li>
        <svg viewBox="0 0 24 24" aria-hidden="true"><path d="M2 5h20v14H2z M3 6l9 7 9-7" /></svg>
        rowan@tbk-plumbing.com.au
      </li>
    </ul>
    <p class="abn">Company ABN - 73 215 904 386</p>
  </section>

  <section class="card card--back">
    <p class="brand__name">TBK</p>
    <p class="brand__tagline">plumbing services</p>
  </section>
</body>
</html>
```